Podiatry clinic requires a modern revamp and editing of existing website.

I would like a fresh new look and updated information for my current business website. An easy to navigate site with prominent address and phone number for call to action. We are a podiatry clinic that focuses on general and sports podiatry.
I would like 4 pages; including Home page, About Us, Services & Contact.
www.brambleridgepodiatry.net

Target Market(s)

Active working professionals.

Industry/Entity Type

Medical

Coding

Coded - Design and coding required

Number of Pages Required

4 page

Font styles to use
Sans Serif

Colors
6b449b

Requirements
Must have
• A modern look with logo and active images; clean and uncluttered. Visible phone number and address for call to action.
• 4 pages - Home, About Us, Services, Contact.
• Home page - update address & service logos.
• About Us - update of personal information.
• Services - Revamp of existing page.
• Contact page to include Google map, email & phone number.
Nice to have
• Ability to add content easily; eg. a blog or adding video onto Home page.
• Link to Facebook page.

```html
<!DOCTYPE html>
<html lang="en">
<head>
<meta charset="utf-8">
<title>Bramble Ridge Podiatry</title>
<link rel="stylesheet" href="https://fonts.googleapis.com/css2?family=Roboto+Condensed:wght@300;400;700&family=Arimo:wght@400;700&family=Great+Vibes&display=swap">
<style>
:root{
  --purple:#6b449b;
  --purple-light:#9b7cc0;
  --purple-soft:#a38ac6;
  --purple-pale:#c3b0de;
  --purple-deep:#5b3a8a;
  --orange:#f08a3a;
  --ink:#222;
  --grey:#666;
  --muted:#999;
  --band:#f1f0f4;
  --footer:#333;
  --footer-deep:#222;
  --footer-link:#888;
  --white:#fff;
}
*{box-sizing:border-box;margin:0;padding:0}
h1,h2,h3,h4{font-weight:400}
html,body{width:1200px;height:2605px;overflow:hidden}
body{position:relative;background:var(--white);font-family:"Arimo",Arial,sans-serif;color:var(--ink)}
.abs{position:absolute}

/* hero */
.hero{left:0;top:0;width:1200px;height:677px;background:linear-gradient(180deg,#4a3a44 0%,#8a5a52 38%,#c07a4e 52%,#3c3434 70%,#2a2a2c 100%)}
.brand{left:78px;top:52px;font-family:"Roboto Condensed",Arial,sans-serif;font-weight:700;font-size:38px;line-height:40px;color:var(--orange);display:flex;align-items:center;gap:12px}
.brand-dot{width:26px;height:26px;border-radius:50%;background:var(--purple)}
.nav{right:80px;top:38px;display:flex;gap:36px;font-family:"Roboto Condensed",Arial,sans-serif;font-size:17px;color:var(--white);text-transform:uppercase}
.nav .active{color:#c8b4ea}
.callus{right:80px;top:92px;font-family:"Roboto Condensed",Arial,sans-serif;font-weight:300;font-size:21px;color:var(--white);display:flex;align-items:center;gap:10px}
.callus b{font-weight:400}
.hero-title{left:0;width:1200px;top:255px;text-align:center;font-family:"Roboto Condensed",Arial,sans-serif;font-size:78px;color:var(--white)}
.hero-rule{left:422px;top:366px;width:356px;height:1px;background:rgba(255,255,255,.7)}
.hero-sub{left:0;width:1200px;top:388px;text-align:center;font-family:"Roboto Condensed",Arial,sans-serif;font-weight:300;font-size:38px;color:var(--white)}
.btn{left:471px;top:465px;width:250px;height:51px;background:var(--purple);color:var(--white);font-size:17px;display:flex;align-items:center;justify-content:center;text-transform:uppercase;border-radius:2px}

/* welcome */
.video{left:78px;top:729px;width:519px;height:313px;background:#6e5b8e}
.video-name{left:0;width:519px;top:90px;text-align:center;font-family:"Roboto Condensed",Arial,sans-serif;font-weight:700;font-size:40px;color:var(--orange)}
.video-play{left:224px;top:150px}
.video-bar{left:0;bottom:0;width:519px;height:28px;background:#111;display:flex;align-items:center;gap:10px;padding:0 10px;color:#ddd;font-size:11px}
.video-track{flex:1;height:6px;background:#eee;border-radius:3px}
.welcome-script{left:636px;width:481px;top:730px;text-align:center;font-family:"Great Vibes",cursive;font-size:40px;color:var(--ink)}
.welcome-title{left:636px;width:481px;top:775px;text-align:center;font-family:"Roboto Condensed",Arial,sans-serif;font-size:40px;color:var(--purple)}
.welcome-text{left:636px;width:481px;top:842px;text-align:center;font-size:13.5px;line-height:22.5px;color:var(--grey)}

/* services */
.svc-top{left:0;top:1094px;width:1200px;height:304px;background:var(--purple)}
.svc-bottom{left:0;top:1400px;width:1200px;height:219px;background:var(--purple-soft)}
.svc-divide{left:0;top:1397px;width:1200px;height:3px;background:var(--white)}
.section-title{left:0;width:1200px;text-align:center;font-family:"Roboto Condensed",Arial,sans-serif;font-size:40px}
.section-title .script{font-family:"Great Vibes",cursive;font-size:42px;margin-right:6px}
.svc-title{top:1138px;color:var(--white)}
.svc-circle{width:153px;height:153px;border-radius:50%;border:3px solid var(--purple-light);box-shadow:0 0 0 4px rgba(255,255,255,.35)}
.svc-head{width:250px;text-align:center;font-family:"Roboto Condensed",Arial,sans-serif;font-size:19px;text-transform:uppercase}
.svc-head-top{color:var(--purple-pale)}
.svc-head-bottom{color:var(--purple-deep)}
.svc-text{width:200px;text-align:center;font-size:13.5px;line-height:22px;color:var(--white)}

/* blog */
.blog-title{top:1660px;color:var(--purple)}
.blog-title .script{color:var(--ink)}
.card{width:332px}
.card-img{width:332px;height:166px;border:1px solid #ddd}
.card-meta{margin-top:14px;font-size:12px;font-style:italic;color:var(--muted);display:flex;align-items:center;gap:8px;padding-bottom:14px;border-bottom:1px solid #eee;width:230px}
.card-head{margin-top:14px;font-size:17px;color:var(--ink)}
.card-text{margin-top:8px;font-size:13.5px;line-height:22px;color:var(--grey)}
.card-more{margin-top:10px;font-size:14px;color:var(--purple);text-transform:uppercase}

/* partners */
.partners{left:0;top:2115px;width:1200px;height:125px;background:var(--band);display:flex;justify-content:space-around;align-items:center;padding:0 100px}
.badge{height:56px;border-radius:6px;background:#d9d4e3}

/* footer */
.footer{left:0;top:2240px;width:1200px;height:313px;background:var(--footer)}
.fcol{top:2272px}
.fhead{font-family:"Roboto Condensed",Arial,sans-serif;font-weight:300;font-size:30px;color:#ccc;margin-bottom:14px}
.flist{list-style:none;width:218px}
.flist li{font-size:13.5px;color:var(--footer-link);padding:9px 0;border-bottom:1px solid #4a4a4a;height:37px;white-space:nowrap}
.flist li:last-child{border-bottom:none}
.flist li.first{color:var(--white)}
.fsplit{left:811px;top:2262px;width:1px;height:270px;background:#555}
.contact-row{display:flex;gap:14px;align-items:flex-start;font-size:13.5px;line-height:22px;color:#ccc;margin-bottom:16px}
.socials{display:flex;gap:12px;margin-top:4px}
.social{width:42px;height:42px;border-radius:50%;background:var(--white)}
.social.outline{background:none;border:1px solid #777}
.copy{left:0;top:2553px;width:1200px;height:52px;background:var(--footer-deep);color:#ccc;font-size:13px;display:flex;align-items:center;justify-content:center;gap:4px}
.copy span{color:#a98bd6}
</style>
</head>
<body>

<header>
  <div class="abs hero" role="img" aria-label="Photo of a runner's legs and shoes on an open road at sunset"></div>
  <div class="abs brand"><span class="brand-dot"></span>bramble ridge podiatry</div>
  <nav class="abs nav"><span class="active">Home</span><span>About Us</span><span>Podiatry Services</span><span>Contact</span></nav>
  <div class="abs callus">
    <svg width="28" height="28" viewBox="0 0 24 24"><path fill="#fff" d="M6.6 10.8a15.1 15.1 0 0 0 6.6 6.6l2.2-2.2c.3-.3.7-.4 1-.2 1.1.4 2.3.6 3.6.6.6 0 1 .4 1 1V20c0 .6-.4 1-1 1C10.6 21 3 13.4 3 4c0-.6.4-1 1-1h3.5c.6 0 1 .4 1 1 0 1.3.2 2.5.6 3.6.1.3 0 .7-.2 1z"/></svg>
    CALL US NOW : <b>1300 555 204</b>
  </div>
  <h1 class="abs hero-title">Don't let pain run your life</h1>
  <div class="abs hero-rule"></div>
  <p class="abs hero-sub">Choose to be pain free</p>
  <a class="abs btn">Book an appointment</a>
</header>

<section class="welcome">
  <div class="abs video" role="img" aria-label="Clinic introduction video poster">
    <div class="abs video-name">bramble ridge podiatry</div>
    <svg class="abs video-play" width="72" height="72" viewBox="0 0 72 72"><circle cx="36" cy="36" r="33" fill="none" stroke="#fff" stroke-width="4"/><path d="M28 20 L52 36 L28 52Z" fill="#fff"/></svg>
    <div class="abs video-bar">
      <svg width="10" height="10" viewBox="0 0 10 10"><path d="M1 0 L10 5 L1 10Z" fill="#fff"/></svg>
      <span>00:00</span><div class="video-track"></div><span>00:42</span>
      <svg width="12" height="12" viewBox="0 0 12 12"><path d="M0 4h3l4-3v10L3 8H0z" fill="#fff"/></svg>
      <svg width="12" height="12" viewBox="0 0 12 12"><path d="M0 4V0h4M8 0h4v4M12 8v4H8M4 12H0V8" fill="none" stroke="#fff" stroke-width="1.5"/></svg>
    </div>
  </div>
  <div class="abs welcome-script">Welcome to</div>
  <h2 class="abs welcome-title">bramble ridge podiatry</h2>
  <p class="abs welcome-text">Bramble Ridge Podiatry is a Podiatry clinic in the heart of Fernvale centre. We are located between Ashgrove &amp; Tilbury Lanes in the Ashgrove Commerce Centre / Linden Court Complex. Our podiatrists are fully qualified health professionals who are able to diagnose, treat, manage or help to prevent all medical conditions that affect the feet and lower limb. We provide General Podiatry Treatment and some Specialised Services in relation to various foot conditions, including Sports Injuries, Orthotic Therapy and Nail Surgery.</p>
</section>

<section class="services">
  <div class="abs svc-top"></div>
  <div class="abs svc-bottom"></div>
  <div class="abs svc-divide"></div>
  <h2 class="abs section-title svc-title"><span class="script">Podiatry</span>Services</h2>

  <div class="abs svc-circle" style="left:127px;top:1234px;background:radial-gradient(circle,#e8d9d2,#c9b3ab)" role="img" aria-label="Photo of a foot during nail surgery"></div>
  <div class="abs svc-head svc-head-top" style="left:276px;top:1238px">Nail Surgery</div>
  <p class="abs svc-text" style="left:311px;top:1272px;width:180px">Minor surgical procedure for the permanent removal of ingrown toenails under local anaesthesia.</p>

  <div class="abs svc-circle" style="left:523px;top:1234px;background:radial-gradient(circle,#e9c8b4,#7fb0c9)" role="img" aria-label="Photo of a podiatrist examining a foot"></div>
  <div class="abs svc-head svc-head-top" style="left:672px;top:1238px">Gait Analysis</div>
  <p class="abs svc-text" style="left:697px;top:1272px">Treadmill analysis of the gait whilst walking or running to ascertain biomechanical problems or abnormalities...</p>

  <div class="abs svc-circle" style="left:919px;top:1234px;background:radial-gradient(circle,#efe3d6,#cdb9a5)" role="img" aria-label="Photo of an orthotic insole under a foot"></div>

  <div class="abs svc-head svc-head-bottom" style="left:78px;top:1427px">Diabetic Management</div>
  <p class="abs svc-text" style="left:108px;top:1461px;width:190px">Assessment of blood supply/circulation with Doppler Ultrasound; Assessment of nerve sensation via Vibration...</p>

  <div class="abs svc-circle" style="left:325px;top:1408px;background:radial-gradient(circle,#e6c6b8,#8a3c6a)" role="img" aria-label="Photo of feet being checked during a diabetic assessment"></div>

  <div class="abs svc-head svc-head-bottom" style="left:474px;top:1413px;line-height:24px">Biomechanical<br>Assessment</div>
  <p class="abs svc-text" style="left:499px;top:1484px">We are able to help diagnose abnormal foot biomechanics that may be contributing to...</p>

  <div class="abs svc-circle" style="left:721px;top:1408px;background:radial-gradient(circle,#e3e6ec,#5a8fc0)" role="img" aria-label="Photo of a patient on a treadmill with tape on the leg"></div>

  <div class="abs svc-head svc-head-bottom" style="left:873px;top:1427px">Orthotic Therapy</div>
  <p class="abs svc-text" style="left:898px;top:1461px">Orthoses, or arch supports, are designed to control the function of the foot when there is evidence of faulty biomechanics.</p>
</section>

<section class="blog">
  <h2 class="abs section-title blog-title"><span class="script">Latest</span>Blog</h2>

  <article class="abs card" style="left:78px;top:1735px">
    <div class="card-img" style="background:linear-gradient(180deg,#f4f1ee,#d9c7b4)" role="img" aria-label="Photo of a person stretching with bare feet"></div>
    <div class="card-meta"><svg width="13" height="13" viewBox="0 0 13 13"><rect x="0.5" y="2" width="12" height="10.5" fill="none" stroke="#a98bd6"/><path d="M0.5 5h12M3.5 0v3M9.5 0v3" stroke="#a98bd6"/></svg>Posted April 5, 2016</div>
    <h3 class="card-head">Lorem Ipsum is simply dummy text of</h3>
    <p class="card-text">Lorem Ipsum is simply dummy text of the printing and typesetting industry.</p>
    <div class="card-more">Read more</div>
  </article>

  <article class="abs card" style="left:434px;top:1735px">
    <div class="card-img" style="background:linear-gradient(180deg,#f5f2ef,#e7dbcf)" role="img" aria-label="Photo of a child resting with bare feet on a bed"></div>
    <div class="card-meta"><svg width="13" height="13" viewBox="0 0 13 13"><rect x="0.5" y="2" width="12" height="10.5" fill="none" stroke="#a98bd6"/><path d="M0.5 5h12M3.5 0v3M9.5 0v3" stroke="#a98bd6"/></svg>Posted April 5, 2016</div>
    <h3 class="card-head">Lorem Ipsum is simply dummy text of</h3>
    <p class="card-text">Lorem Ipsum is simply dummy text of the printing and typesetting industry.</p>
    <div class="card-more">Read more</div>
  </article>

  <article class="abs card" style="left:790px;top:1735px">
    <div class="card-img" style="background:linear-gradient(180deg,#7cb65a,#3e7d2e)" role="img" aria-label="Photo of a football player kicking a ball on grass"></div>
    <div class="card-meta"><svg width="13" height="13" viewBox="0 0 13 13"><rect x="0.5" y="2" width="12" height="10.5" fill="none" stroke="#a98bd6"/><path d="M0.5 5h12M3.5 0v3M9.5 0v3" stroke="#a98bd6"/></svg>Posted April 5, 2016</div>
    <h3 class="card-head">Lorem Ipsum is simply dummy text of</h3>
    <p class="card-text">Lorem Ipsum is simply dummy text of the printing and typesetting industry.</p>
    <div class="card-more">Read more</div>
  </article>
</section>

<section class="abs partners">
  <div class="badge" style="width:160px"></div>
  <div class="badge" style="width:160px"></div>
  <div class="badge" style="width:205px"></div>
  <div class="badge" style="width:225px"></div>
</section>

<footer>
  <div class="abs footer"></div>

  <div class="abs fcol" style="left:78px">
    <h4 class="fhead">Usefull links</h4>
    <ul class="flist" style="width:170px"><li class="first">Home</li><li>About us</li><li>Services</li><li>Contact</li></ul>
  </div>
  <div class="abs fcol" style="left:278px">
    <h4 class="fhead">Treatments</h4>
    <ul class="flist"><li class="first">Diabetic Management</li><li>Nail Surgery</li><li>Biomechanical Assessment</li><li>Gait Analysis</li><li>Orthotic Therapy</li></ul>
  </div>
  <div class="abs fcol" style="left:526px">
    <h4 class="fhead">Products</h4>
    <ul class="flist" style="width:230px"><li class="first">Softstep Heel Repair Balm</li><li>Trailguard Anti-Chafe Stick</li><li>Meadowleaf Foot Scrub &amp; Oil</li><li>Mossvale Cooling Cream &amp; Spray</li><li>Clearpath Antifungal Skin Cream</li></ul>
  </div>
  <div class="abs fsplit"></div>
  <div class="abs fcol" style="left:853px">
    <h4 class="fhead">Contact Information</h4>
    <div class="contact-row">
      <svg width="20" height="24" viewBox="0 0 20 24"><path d="M10 1a8 8 0 0 0-8 8c0 6 8 14 8 14s8-8 8-14a8 8 0 0 0-8-8z" fill="none" stroke="#aaa" stroke-width="1.5"/><circle cx="10" cy="9" r="3" fill="none" stroke="#aaa" stroke-width="1.5"/></svg>
      <span>Suite 12 / 75 Ashgrove Lane<br>Fernvale 3150.</span>
    </div>
    <div class="contact-row">
      <svg width="20" height="20" viewBox="0 0 24 24"><path fill="none" stroke="#aaa" stroke-width="1.5" d="M6.6 10.8a15.1 15.1 0 0 0 6.6 6.6l2.2-2.2c.3-.3.7-.4 1-.2 1.1.4 2.3.6 3.6.6.6 0 1 .4 1 1V20c0 .6-.4 1-1 1C10.6 21 3 13.4 3 4c0-.6.4-1 1-1h3.5c.6 0 1 .4 1 1 0 1.3.2 2.5.6 3.6.1.3 0 .7-.2 1z"/></svg>
      <span>1300 555 204</span>
    </div>
    <div class="contact-row">
      <svg width="20" height="16" viewBox="0 0 20 16"><rect x="1" y="1" width="18" height="14" fill="none" stroke="#aaa" stroke-width="1.5"/><path d="M1 1l9 7 9-7" fill="none" stroke="#aaa" stroke-width="1.5"/></svg>
      <span>info@brambleridgepodiatry.net</span>
    </div>
    <div class="socials"><div class="social outline"></div><div class="social"></div><div class="social"></div></div>
  </div>

  <div class="abs copy">© <span>bramble ridge podiatry</span> - 2016. All Rights Reserved.</div>
</footer>

</body>
</html>
```